Web Design Project

The aim of this project to design a website for a service that would offer services for small business and non profit organizations using opensource software that is weaved to work together in harmony.

The website name is: vestolia.net

Vestolia in Arabic means: cabbage. Cabbage is composed of leaves, actually there is nothing except leaves. Each leave by itself is not called cabbage, but a collection of leaves that are organized in a central way would give us cabbage.

Same idea for Vestolia where open source software very well organized and integrated would create a new thing with a new value.

Target Market(s)

Small business, Europe, Africa, Far east and Middle east

Industry/Entity Type

Small Business

Requirements
Must have
• The website would offer the following sections:
* Home page
* Benefits: value of vestolia
* Applications: applications offered by vestolia
* Pricing
* Purchase
* Customer log in
* Support
- FAQ
- Knowledge base
- Forums
- Open tickets

Please take the following consideration in design:
* White should predominate
* Only black and the colors of logo are permitted (attched)
Nice to have
• Design is better to express:
* Openness
* Dynamic
* Usable
* Cost effective

```html
<!DOCTYPE html>
<html lang="en">
<head>
<meta charset="utf-8">
<title>Vestolia</title>
<link rel="stylesheet" href="https://fonts.googleapis.com/css2?family=Questrial&display=swap">
<style>
:root{
  --ink:#222;
  --text:#555;
  --muted:#777;
  --line:#999;
  --green:#8cbf26;
  --magenta:#b5509e;
  --magenta-soft:rgba(181,80,158,.78);
  --blue:rgba(38,145,200,.85);
  --nav-active:#7a7a7a;
  --bg:#fff;
}
*{margin:0;padding:0;box-sizing:border-box}
html,body{width:1123px;height:1200px;overflow:hidden;background:var(--bg)}
body{font-family:"Questrial",sans-serif;color:var(--text);position:relative}
.abs{position:absolute}
.brand{left:55px;top:20px;display:flex;align-items:center;gap:12px}
.brand-mark{width:34px;height:34px;border-radius:50%;background:var(--magenta)}
.brand-name{font-size:44px;color:var(--ink);letter-spacing:-1px;line-height:1}
.brand{top:70px}
.top-links{left:576px;top:102px;font-size:16px;color:var(--muted)}
.top-links span{margin:0 6px}
.welcome{left:874px;top:98px;display:flex;align-items:center;gap:8px;font-size:16px;color:var(--muted)}
.welcome b{font-weight:normal;color:var(--green)}
.main-nav{left:55px;top:156px;width:1023px;height:30px;border-top:1px solid var(--line);border-bottom:1px solid var(--line);display:flex;align-items:center}
.main-nav a{font-size:16px;color:var(--text);text-decoration:none;padding:0 13px;height:100%;display:flex;align-items:center}
.main-nav a.active{background:var(--nav-active);color:#fff;padding:0 8px}
.search{margin-left:auto;display:flex;align-items:center;gap:34px;padding-right:10px;font-size:14px;font-style:italic;color:#999}
.hero-main{left:55px;top:216px;width:677px;height:357px;background:linear-gradient(120deg,#8a4a1c,#d9a05a 40%,#e8cfa6 60%,#6b4a2a)}
.hero-main .note{position:absolute;left:441px;top:14px;width:222px;height:160px;background:var(--magenta-soft);color:#fff;font-size:16px;line-height:23.5px;padding:22px 11px}
.hero-main .band{position:absolute;left:0;bottom:0;width:100%;height:71px;background:var(--magenta-soft);color:#fff;font-size:16px;line-height:23.5px;text-align:center;padding-top:12px}
.hero-side{left:746px;top:216px;width:331px;height:359px;background:linear-gradient(180deg,#e9eef1,#cfd7dc 45%,#8b5a3a 60%,#6b4a36)}
.hero-side .band{position:absolute;left:0;bottom:0;width:100%;height:126px;background:var(--blue);color:#fff;font-size:16px;line-height:23.5px;padding:30px 19px}
.section-title{left:56px;top:612px;font-size:22px;color:var(--muted);letter-spacing:.5px}
.product{width:240px;top:649px}
.product .shot{height:161px;border:1px solid #ddd}
.product p{margin-top:14px;font-size:16px;line-height:23.5px;color:var(--text)}
.shot.cart{background:#b56fae;position:relative;color:#fff;font-size:16px}
.shot.cart svg{position:absolute;left:78px;top:30px}
.shot.cart span{position:absolute;left:69px;top:97px}
.shot.clinic{background:linear-gradient(135deg,#dfe6ea,#c8d4d8 50%,#9fb8bf)}
.shot.cloud{background:linear-gradient(180deg,#f4f6f8,#e8eef2)}
.shot.tech{background:radial-gradient(circle at 60% 45%,#5ab3d4,#1d3a4e 60%,#101820)}
.footer-col{top:980px;font-size:13px;line-height:19px;color:var(--text)}
.footer-col h3{font-weight:normal;font-size:16px;color:var(--muted);margin-bottom:11px}
.newsletter{left:839px;top:980px;font-size:13px;line-height:16px;color:var(--text)}
.newsletter .field{margin-top:12px;width:207px;height:26px;border:1px solid #ccc;display:flex;align-items:center;justify-content:space-between;padding:0 5px;color:#888;font-size:13px}
.newsletter .go{width:17px;height:16px;border:1px solid #aaa;border-radius:2px;display:flex;align-items:center;justify-content:center}
.legal{left:55px;top:1160px;font-size:13px;color:var(--text)}
</style>
</head>
<body>

<header>
  <div class="abs brand"><span class="brand-mark"></span><span class="brand-name">vestolia</span></div>
  <div class="abs top-links">Log In<span>|</span>Register<span>|</span>Support<span>|</span>FAQ</div>
  <div class="abs welcome">
    <svg width="20" height="24" viewBox="0 0 20 24"><circle cx="10" cy="4" r="3.5" fill="#888"/><path d="M2 24V11q0-3 3-3h10q3 0 3 3v13h-4V14h-1v10H7V14H6v10z" fill="#888"/></svg>
    WELCOME <b>YOURNAME</b>
  </div>
  <nav class="abs main-nav">
    <a class="active">home</a><a>benefits</a><a>applications</a><a>pricing</a><a>purchase</a><a>knowledge base</a><a>forums</a><a>open tickets</a>
    <div class="search">search for something here
      <svg width="20" height="20" viewBox="0 0 20 20"><circle cx="8" cy="8" r="6" fill="none" stroke="#888" stroke-width="2.4"/><path d="M12.5 12.5l6 6" stroke="#888" stroke-width="2.8" stroke-linecap="round"/></svg>
    </div>
  </nav>
</header>

<section class="abs hero-main" role="img" aria-label="Smiling young woman outdoors in autumn light">
  <div class="note">Lorem ipsum dolor sit amet, consectetur adipisci elit. Nunc elit erat, tincidunt quis tempus vel, iaculis quis ligula.</div>
  <div class="band">Lorem ipsum dolor sit amet, consectetur adipiscing elit.<br>Nunc elit erat, tincidunt quis tempus vel, iaculis quis ligula.</div>
</section>
<section class="abs hero-side" role="img" aria-label="Family on a sofa with a laptop">
  <div class="band">Lorem ipsum dolor sit amet, consectetur adipiscing elit. Nunc elit erat, tincidunt quis tempus vel, iaculis quis ligula.</div>
</section>

<h2 class="abs section-title">NEW PRODUCTS</h2>

<article class="abs product" style="left:55px">
  <div class="shot cart" role="img" aria-label="Devices and components behind an add to cart icon">
    <svg width="70" height="56" viewBox="0 0 70 56"><path d="M2 4h9l8 30h38l8-22H15" fill="none" stroke="#fff" stroke-width="4" stroke-linejoin="round"/><circle cx="25" cy="48" r="5" fill="#fff"/><circle cx="51" cy="48" r="5" fill="#fff"/></svg>
    <span>Add to cart</span>
  </div>
  <p>Lorem ipsum dolor sit amet, con­sectetur adipiscing elit. Nunc elit erat, tincidunt quis tempus vel, iaculis quis ligula.</p>
</article>
<article class="abs product" style="left:316px">
  <div class="shot clinic" role="img" aria-label="Medical staff in a hospital room"></div>
  <p>Lorem ipsum dolor sit amet, con­sectetur adipiscing elit. Nunc elit erat, tincidunt quis tempus vel, iaculis quis ligula.</p>
</article>
<article class="abs product" style="left:577px">
  <div class="shot cloud" role="img" aria-label="Blue cloud above a laptop"></div>
  <p>Lorem ipsum dolor sit amet, con­sectetur adipiscing elit. Nunc elit erat, tincidunt quis tempus vel, iaculis quis ligula.</p>
</article>
<article class="abs product" style="left:839px">
  <div class="shot tech" role="img" aria-label="Hand touching floating digital icons in a server room"></div>
  <p>Lorem ipsum dolor sit amet, con­sectetur adipiscing elit. Nunc elit erat, tincidunt quis tempus vel, iaculis quis ligula.</p>
</article>

<footer>
  <div class="abs footer-col" style="left:55px"><h3>INFORMATION</h3>Terms and Conditions<br>Privacy Policy<br>About Us</div>
  <div class="abs footer-col" style="left:316px"><h3>YOUR ACCOUNT</h3>Log In<br>Register<br>Newsletter Subscriptions</div>
  <div class="abs footer-col" style="left:577px"><h3>CONTACTS</h3>
    <div style="line-height:25px">Lorem ipsum dolor sit amet,<br>consectetur adipiscing elit.</div>
    <div style="margin-top:12px">Telephone: +00 00000<br>000000<br>E-mail: mail@yoursite.com</div>
  </div>
  <div class="abs newsletter">Subscribe to our free monthly<br>newsletter and be the first<br>to hear about our offers.
    <div class="field">Email..<span class="go"><svg width="6" height="8" viewBox="0 0 6 8"><path d="M1 1l4 3-4 3" fill="none" stroke="#888" stroke-width="1.4"/></svg></span></div>
  </div>
  <div class="abs legal">© 2013 All Rights Reserved</div>
</footer>

</body>
</html>
```